Business Card Design

We are a manufacturing and distribution company with most of our customer base being supermarkets. We have established brand guidelines that are attached.

```html
<!DOCTYPE html>
<html lang="en">
<head>
<meta charset="utf-8">
<title>Velmont Business Card</title>
<link rel="stylesheet" href="https://fonts.googleapis.com/css2?family=Archivo:wght@700;800&family=Arimo:wght@400;700&display=swap">
<style>
  :root {
    --backdrop: #e8e8e6;
    --card-white: #ffffff;
    --brand-blue: #0b62ad;
    --brand-blue-light: #1f7fd1;
    --brand-blue-deep: #084d8c;
    --brand-red: #e0202a;
    --ink: #1b1b1b;
    --muted: #6f6f6f;
  }
  * { margin: 0; padding: 0; box-sizing: border-box; }
  html, body {
    width: 1200px; height: 802px; overflow: hidden;
    background: var(--backdrop);
  }
  .stage {
    width: 1200px; height: 802px;
    display: flex; align-items: center; justify-content: center; gap: 40px;
  }
  .card {
    width: 540px; height: 309px; position: relative; overflow: hidden;
    border-bottom: 4px solid var(--brand-red);
    box-shadow: 0 10px 24px rgba(0,0,0,0.14);
  }
  /* front */
  .card--front { background: var(--card-white); }
  .front__mark {
    position: absolute; right: 40px; top: 70px;
    display: flex; align-items: center; gap: 12px;
  }
  .front__mark-square { width: 44px; height: 44px; background: var(--brand-red); }
  .front__mark-name {
    font-family: "Archivo", sans-serif; font-weight: 800; font-size: 34px;
    color: var(--brand-blue); letter-spacing: 1px;
  }
  .front__details { position: absolute; left: 36px; bottom: 32px; }
  .front__brand {
    font-family: "Archivo", sans-serif; font-weight: 800; font-size: 28px;
    color: var(--ink); letter-spacing: 1.5px; margin-bottom: 12px;
  }
  .front__person {
    font-family: "Archivo", sans-serif; font-weight: 700; font-size: 15px;
    color: var(--brand-red); letter-spacing: 0.8px;
  }
  .front__role { font-family: "Arimo", sans-serif; font-size: 13px; color: var(--muted); margin-bottom: 12px; }
  .front__address { font-family: "Arimo", sans-serif; font-size: 12.5px; color: var(--muted); line-height: 1.35; margin-bottom: 10px; }
  .contact-list { list-style: none; font-family: "Arimo", sans-serif; font-size: 12.5px; color: var(--muted); line-height: 1.5; }
  .contact-list li { display: flex; align-items: center; gap: 8px; }
  .contact-list svg { width: 11px; height: 11px; flex: none; }
  /* back */
  .card--back { background: var(--brand-blue); }
  .back__texture {
    position: absolute; inset: 0;
    background: linear-gradient(135deg, var(--brand-blue-deep) 0%, var(--brand-blue) 45%, var(--brand-blue-light) 100%);
  }
  .back__mark {
    position: absolute; left: 50%; top: 50%; transform: translate(-50%, -50%);
    display: flex; align-items: center; gap: 14px;
  }
  .back__mark-square { width: 34px; height: 34px; background: var(--brand-red); }
  .back__mark-name {
    font-family: "Archivo", sans-serif; font-weight: 800; font-size: 30px;
    color: var(--card-white); letter-spacing: 2px;
  }
</style>
</head>
<body>
<main class="stage">
  <section class="card card--front" aria-label="Card front">
    <div class="front__mark">
      <span class="front__mark-square"></span>
      <span class="front__mark-name">VELMONT</span>
    </div>
    <div class="front__details">
      <h1 class="front__brand">VELMONT</h1>
      <p class="front__person">DANIEL HART</p>
      <p class="front__role">Manager</p>
      <p class="front__address">Your address, city<br>state, ZIP 0000</p>
      <ul class="contact-list">
        <li>
          <svg viewBox="0 0 12 12"><path d="M2 1h3l1 3-1.5 1a6 6 0 0 0 2.5 2.5L8 6l3 1v3a1 1 0 0 1-1 1A9 9 0 0 1 1 2a1 1 0 0 1 1-1z" fill="var(--brand-red)"/></svg>
          555-014-2100
        </li>
        <li>
          <svg viewBox="0 0 12 12"><rect x="1" y="2.5" width="10" height="7" fill="none" stroke="var(--brand-red)" stroke-width="1.3"/><path d="M1 2.5l5 4 5-4" fill="none" stroke="var(--brand-red)" stroke-width="1.3"/></svg>
          hello@velmont-mail.com
        </li>
        <li>
          <svg viewBox="0 0 12 12"><circle cx="6" cy="6" r="5" fill="none" stroke="var(--brand-red)" stroke-width="1.3"/><path d="M1 6h10M6 1c-2.5 3-2.5 7 0 10M6 1c2.5 3 2.5 7 0 10" fill="none" stroke="var(--brand-red)" stroke-width="1"/></svg>
          www.velmont-goods.com
        </li>
      </ul>
    </div>
  </section>

  <section class="card card--back" aria-label="Card back">
    <div class="back__texture" role="img" aria-label="Embossed repeating brand-mark pattern in blue tones"></div>
    <div class="back__mark">
      <span class="back__mark-square"></span>
      <span class="back__mark-name">VELMONT</span>
    </div>
  </section>
</main>
</body>
</html>
```